Brand new letterhead, business card, email signature etc.

We are a financial company in London, UK. Our website is www.marlowvane.com. We're wanting a complete remodel of the company colours, letter head, business cards, email signatures, etc. Looking to keep the same font for the company name. I have upload a colour palette that we want to work with. We're looking for company letterhead for outgoing letters/ correspondence, letterhead for internal documentation, email signatures, e-letters. etc. Ultimately we will redesign the entire website also. It is important that our clients get a strong, secure, warm, trustworthy, solid feeling and first impression.
Updates

Designs look the same

Target Market(s)

Institutional investors, (ultra) high net worth individuals

Industry/Entity Type

Finance, Invesments banking.

Font styles to use
Other font styles liked:
• Current font is "Champagne & Limousines"

Requirements
Must have
• Must use the colours provided on the PDF uploaded to the portal. The purple = main colour. The red = accent colour.
Nice to have
• Nice to use same font as now for the company name "Corvane". Font is "Champagne & Limousines". Nice to have some reference to the old logo flower, but only subtle.
Should not have
• Do not use the colour red from our website. Use the colours provided on the colour palette PDF that I uploaded in the portal.

```html
<!DOCTYPE html>
<html lang="en">
<head>
<meta charset="utf-8">
<title>Corvane – Business Card</title>
<link href="https://fonts.googleapis.com/css2?family=Jost:wght@300;500&family=PT+Sans&display=swap" rel="stylesheet">
<style>
  :root {
    --backdrop: #9a9a9a;
    --card-white: #f6f6f5;
    --card-black: #141414;
    --edge-red: #a3101c;
    --ink: #262626;
    --ink-soft: #555555;
    --accent: #c0213f;
    --foil: #c9c9c9;
  }
  * { margin: 0; padding: 0; box-sizing: border-box; }
  html, body {
    width: 1200px; height: 1084px; overflow: hidden;
    background: var(--backdrop);
  }
  .stage {
    width: 1200px; height: 1084px;
    display: flex; flex-direction: column; align-items: center; justify-content: center;
    gap: 70px;
  }
  .card {
    position: relative;
    width: 700px; height: 400px;
    border-bottom: 5px solid var(--edge-red);
  }
  .card--front { background: var(--card-white); }
  .card--back {
    background: var(--card-black);
    display: flex; align-items: center; justify-content: center;
  }
  .brand {
    display: flex; align-items: center; gap: 26px;
  }
  .brand__square {
    width: 92px; height: 92px;
    border: 1.5px solid var(--ink);
  }
  .brand__name {
    font-family: "Jost", sans-serif;
    font-weight: 300;
    font-size: 46px;
    letter-spacing: 0.32em;
    color: var(--ink);
  }
  .card--front .brand { position: absolute; left: 70px; top: 50px; }
  .card--back .brand__square { border-color: var(--foil); width: 120px; height: 120px; }
  .card--back .brand__name { color: var(--foil); font-size: 56px; }
  .holder {
    position: absolute; left: 70px; top: 190px;
  }
  .holder__name {
    font-family: "Jost", sans-serif;
    font-weight: 500;
    font-size: 24px;
    letter-spacing: 0.01em;
    color: var(--ink);
    text-transform: uppercase;
  }
  .holder__role {
    font-family: "Jost", sans-serif;
    font-weight: 300;
    font-size: 18px;
    color: var(--accent);
    margin-top: 2px;
  }
  .contact {
    position: absolute; left: 70px; top: 275px;
    font-family: "PT Sans", sans-serif;
    font-size: 14px;
    letter-spacing: 0.06em;
    line-height: 1.65;
    color: var(--ink-soft);
  }
  .contact__row { display: flex; align-items: center; gap: 18px; margin-top: 2px; }
  .contact__item { display: flex; align-items: center; gap: 6px; }
  .contact__icon { width: 16px; height: 16px; flex: none; }
</style>
</head>
<body>
<main class="stage">
  <section class="card card--front">
    <div class="brand">
      <div class="brand__square"></div>
      <span class="brand__name">CORVANE</span>
    </div>
    <div class="holder">
      <p class="holder__name">Adrian L. Thorne</p>
      <p class="holder__role">Founder &amp; CEO</p>
    </div>
    <div class="contact">
      <p>Corvane (IOM) Limited, Harbour Court, Ramsey, Isle of Man, IM98 2QT</p>
      <p>Corvane Group Limited, 9th Floor, 14 Ledger Row, London, EC3N 7HL</p>
      <div class="contact__row">
        <span class="contact__item">
          <svg class="contact__icon" viewBox="0 0 16 16" aria-hidden="true">
            <circle cx="8" cy="8" r="7" fill="none" stroke="var(--accent)" stroke-width="1.3"/>
            <path d="M5.3 4.5c.6-.4 1-.3 1.3.2l.6 1.2c.2.4 0 .7-.3 1l-.3.3c.4.9 1 1.6 1.9 2l.3-.3c.3-.3.6-.4 1-.2l1.1.6c.5.3.6.7.2 1.2-.7.9-1.7 1-2.9.3-1.6-.9-2.8-2.3-3.3-3.9-.3-.9 0-1.7.4-2.4z" fill="var(--accent)"/>
          </svg>
          (020) 555-0148
        </span>
        <span class="contact__item">
          <svg class="contact__icon" viewBox="0 0 16 16" aria-hidden="true">
            <circle cx="8" cy="8" r="7" fill="none" stroke="var(--accent)" stroke-width="1.3"/>
            <rect x="4.2" y="5.3" width="7.6" height="5.4" fill="var(--accent)"/>
            <path d="M4.2 5.5 8 8.4l3.8-2.9" fill="none" stroke="var(--card-white)" stroke-width="0.8"/>
          </svg>
          info@marlowvane.com
        </span>
        <span class="contact__item">
          <svg class="contact__icon" viewBox="0 0 16 16" aria-hidden="true">
            <circle cx="8" cy="8" r="7" fill="none" stroke="var(--accent)" stroke-width="1.3"/>
            <circle cx="8" cy="8" r="4" fill="none" stroke="var(--accent)" stroke-width="1"/>
            <path d="M4 8h8M8 4c-1.6 2.4-1.6 5.6 0 8M8 4c1.6 2.4 1.6 5.6 0 8" fill="none" stroke="var(--accent)" stroke-width="0.8"/>
          </svg>
          www.marlowvane.com
        </span>
      </div>
    </div>
  </section>

  <section class="card card--back">
    <div class="brand">
      <div class="brand__square"></div>
      <span class="brand__name">CORVANE</span>
    </div>
  </section>
</main>
</body>
</html>
```